Awesome Business Card Design needed!

Hey there.
I'm looking for a simple but awesome business card design.
Type of company: Online advertisement agency
(please don't use the typical business people or statistics images on the card)
The front has to display the business name
and possibly some sort of logo ( perhaps something with the two M's of the biz name )
And the back of the card should say:
Name
Phone
Email
Let your imagination flow.
here are some designs that I like and that you can use as inspiration.
Simple but Awesome
http://images.lumavexo.com/designs/55128_877673_43091_thumbnail.jpg
http://images.lumavexo.com/designs/37714_747642_40106_image.jpg
http://images.lumavexo.com/designs/55128_877673_43091_image.jpg
http://images.lumavexo.com/designs/51321_781878_43091_image.jpg
http://images.lumavexo.com/designs/33378_399063_15912_image.jpg
http://images.lumavexo.com/designs/2337_271604_9495_image.jpg
good luck

```html
<!DOCTYPE html>
<html lang="en">
<head>
<meta charset="utf-8">
<title>Velora Media – Business Card</title>
<link rel="stylesheet" href="https://fonts.googleapis.com/css2?family=Tinos:wght@400;700&family=Arimo:wght@400&display=swap">
<style>
  :root {
    --page-bg: #e9e6e2;
    --card-black: #060708;
    --card-gloss: #2f3031;
    --card-white: #ffffff;
    --teal: #0f8aa8;
    --teal-light: #2aa3bf;
    --ink: #111111;
    --tag-white: #e8e8e8;
  }
  * { box-sizing: border-box; margin: 0; padding: 0; }
  html, body {
    width: 1200px; height: 900px; overflow: hidden;
    background: var(--page-bg);
  }
  .stage {
    position: relative; width: 1200px; height: 900px;
    display: flex; flex-direction: column; align-items: center; justify-content: center; gap: 60px;
  }
  .card {
    position: relative; width: 600px; height: 345px;
    border-radius: 26px; overflow: hidden;
    box-shadow: 0 10px 24px rgba(0,0,0,.25);
  }
  .card-art { position: absolute; inset: 0; width: 100%; height: 100%; display: block; }

  /* front */
  .front-brand {
    position: absolute; left: 0; right: 0; top: 132px;
    display: flex; flex-direction: column; align-items: center;
  }
  .brand-row { display: flex; align-items: center; gap: 14px; white-space: nowrap; }
  .brand-mark { width: 22px; height: 22px; background: var(--teal-light); flex: none; }
  .brand-name {
    font-family: "Tinos", "Times New Roman", serif;
    font-size: 44px; letter-spacing: 1px; color: var(--teal); line-height: 1;
  }
  .brand-tagline {
    margin-top: 10px;
    font-family: "Tinos", "Times New Roman", serif;
    font-size: 22px; color: var(--tag-white); letter-spacing: .5px;
    white-space: nowrap;
  }

  /* back */
  .back-brand {
    position: absolute; left: 26px; top: 150px; width: 250px;
  }
  .back-brand .brand-name { font-size: 27px; letter-spacing: .5px; }
  .back-brand .brand-mark { width: 15px; height: 15px; }
  .back-brand .brand-row { gap: 9px; }
  .back-brand .brand-tagline { font-size: 16px; margin-top: 6px; }

  .holder { position: absolute; left: 400px; top: 52px; }
  .holder-name {
    font-family: "Tinos", "Times New Roman", serif;
    font-size: 32px; color: var(--teal); line-height: 1;
    white-space: nowrap;
  }
  .holder-role {
    margin-top: 4px;
    font-family: "Tinos", "Times New Roman", serif;
    font-size: 17px; color: var(--ink);
  }
  .contact-list {
    position: absolute; left: 340px; bottom: 40px;
    list-style: none; display: flex; flex-direction: column; gap: 20px;
  }
  .contact-item {
    display: flex; align-items: center; gap: 10px;
    font-family: "Arimo", Arial, sans-serif; font-size: 17px; color: var(--teal);
    white-space: nowrap;
  }
  .contact-icon { width: 20px; height: 20px; flex: none; }
</style>
</head>
<body>
<main class="stage">

  <section class="card card-front" aria-label="Business card front">
    <svg class="card-art" viewBox="0 0 600 345" preserveAspectRatio="none" aria-hidden="true">
      <rect width="600" height="345" fill="var(--card-black)"/>
      <path d="M0 0 H600 V60 C420 110 200 150 0 250 Z" fill="var(--card-gloss)"/>
    </svg>
    <div class="front-brand">
      <div class="brand-row">
        <span class="brand-mark"></span>
        <span class="brand-name">VELORA MEDIA</span>
      </div>
      <p class="brand-tagline">Online advertisement agency</p>
    </div>
  </section>

  <section class="card card-back" aria-label="Business card back">
    <svg class="card-art" viewBox="0 0 600 345" preserveAspectRatio="none" aria-hidden="true">
      <rect width="600" height="345" fill="var(--card-white)"/>
      <path d="M0 0 H345 C305 120 285 230 282 345 H0 Z" fill="var(--card-black)"/>
      <path d="M356 0 H368 C330 120 312 230 310 345 H292 C298 230 318 120 356 0 Z" fill="var(--teal)"/>
    </svg>

    <div class="back-brand">
      <div class="brand-row">
        <span class="brand-mark"></span>
        <span class="brand-name">VELORA MEDIA</span>
      </div>
      <p class="brand-tagline">Online advertisement agency</p>
    </div>

    <div class="holder">
      <p class="holder-name">Your Name</p>
      <p class="holder-role">Company Position</p>
    </div>

    <ul class="contact-list">
      <li class="contact-item">
        <svg class="contact-icon" viewBox="0 0 20 20" aria-hidden="true">
          <circle cx="10" cy="10" r="10" fill="var(--teal)"/>
          <path d="M7 5.5 L8.6 5.2 L9.4 7.6 L8.3 8.4 C8.8 9.8 9.9 11 11.3 11.6 L12.1 10.5 L14.5 11.3 L14.2 12.9 C10 13.4 6.5 9.8 7 5.5 Z" fill="#fff"/>
        </svg>
        <span>000 000 0000</span>
      </li>
      <li class="contact-item">
        <svg class="contact-icon" viewBox="0 0 20 20" aria-hidden="true">
          <circle cx="10" cy="10" r="10" fill="var(--teal)"/>
          <rect x="5" y="6.5" width="10" height="7" fill="#fff"/>
          <path d="M5 6.5 L10 10.5 L15 6.5" fill="none" stroke="var(--teal)" stroke-width="1"/>
        </svg>
        <span>name@domainname.com</span>
      </li>
    </ul>
  </section>

</main>
</body>
</html>
```